Business Card Design

We need a business card designed for our new company. Prefer a black card with white logo & writing.

Contact Information for Business Card

Ted Galloway, address: 7-4812 Fernhollow Road, Abbotsford, BC, V3K 8R2, Office Phone: 604-712-3390, Cell: 604-947-2164, Email: ted@resinworkshub.ca

Colors

Designer to choose only greyscale colors for use in the design.

```html
<!DOCTYPE html>
<html lang="en">
<head>
<meta charset="utf-8">
<title>Resin Works Hub – Business Card</title>
<link rel="stylesheet" href="https://fonts.googleapis.com/css2?family=Figtree:wght@400;600;800&display=swap">
<style>
  :root {
    --bg: #1e1e1e;
    --card: #000000;
    --ink-light: #ffffff;
    --ink-dark: #111111;
    --mid-grey: #444444;
    --rule: #222222;
  }
  * { margin: 0; padding: 0; box-sizing: border-box; }
  html, body { width: 1200px; height: 900px; overflow: hidden; }
  body {
    background: var(--bg);
    font-family: "Figtree", "Helvetica Neue", Arial, sans-serif;
    position: relative;
  }
  .card {
    position: absolute;
    left: 341px;
    width: 518px;
    height: 296px;
    background: var(--card);
    overflow: hidden;
  }
  .card--front { top: 141px; }
  .card--back { top: 463px; }

  .peak-art {
    position: absolute;
    left: 0; top: 26px;
    width: 518px; height: 270px;
  }
  .holder-name {
    position: absolute;
    left: 27px; top: 57px;
    color: var(--ink-light);
    font-weight: 800;
    font-size: 18px;
    letter-spacing: 0.2px;
    text-transform: uppercase;
  }
  .brand-name {
    position: absolute;
    right: 26px; top: 58px;
    color: var(--ink-light);
    font-weight: 800;
    font-size: 15px;
    letter-spacing: 0.3px;
    text-transform: uppercase;
  }
  .contact {
    position: absolute;
    top: 218px;
    color: var(--ink-dark);
    font-size: 14px;
    line-height: 18px;
    list-style: none;
  }
  .contact--direct { left: 28px; }
  .contact--location { left: 229px; }
  .contact li { display: flex; align-items: center; gap: 6px; height: 18px; }
  .contact .icon { width: 12px; height: 12px; flex: none; }
  .contact .web strong { font-weight: 800; }
  .divider {
    position: absolute;
    left: 211px; top: 222px;
    width: 1px; height: 48px;
    background: var(--rule);
  }
  .brand-name--large {
    position: absolute;
    left: 0; right: 0; top: 124px;
    text-align: center;
    color: var(--ink-light);
    font-weight: 800;
    font-size: 38px;
    letter-spacing: 0.5px;
    text-transform: uppercase;
  }
</style>
</head>
<body>
  <section class="card card--front">
    <svg class="peak-art" role="img" aria-label="Mountain peak illustration in black, grey and white" viewBox="0 0 518 270">
      <defs>
        <linearGradient id="peakTone" x1="0" y1="0" x2="0" y2="1">
          <stop offset="0" stop-color="#000000"/>
          <stop offset="0.4" stop-color="#444444"/>
          <stop offset="0.72" stop-color="#ffffff"/>
          <stop offset="1" stop-color="#ffffff"/>
        </linearGradient>
      </defs>
      <rect width="518" height="270" fill="url(#peakTone)"/>
    </svg>

    <h1 class="holder-name">Ted Galloway</h1>
    <p class="brand-name">Resin Works Hub</p>

    <ul class="contact contact--direct">
      <li>
        <svg class="icon" viewBox="0 0 24 24"><path fill="#111" d="M6.6 10.8a15.1 15.1 0 0 0 6.6 6.6l2.2-2.2c.3-.3.7-.4 1-.2 1.1.4 2.3.6 3.6.6.6 0 1 .4 1 1V20c0 .6-.4 1-1 1A17 17 0 0 1 3 4c0-.6.4-1 1-1h3.5c.6 0 1 .4 1 1 0 1.3.2 2.5.6 3.6.1.3 0 .7-.2 1l-2.3 2.2z"/></svg>
        604-712-3390
      </li>
      <li>
        <svg class="icon" viewBox="0 0 24 24"><rect x="6" y="1.5" width="12" height="21" rx="2" fill="none" stroke="#111" stroke-width="2"/><circle cx="12" cy="18.5" r="1.2" fill="#111"/></svg>
        604-947-2164
      </li>
      <li>
        <svg class="icon" viewBox="0 0 24 24"><path fill="#111" d="M2 5h20v14H2z"/><path fill="none" stroke="#fff" stroke-width="1.6" d="M2.5 5.5 12 13l9.5-7.5"/></svg>
        ted@resinworkshub.ca
      </li>
    </ul>

    <div class="divider"></div>

    <ul class="contact contact--location">
      <li>7-4812 Fernhollow Road</li>
      <li>Abbotsford, BC, V3K 8R2</li>
      <li class="web">
        <svg class="icon" viewBox="0 0 24 24"><g fill="none" stroke="#111" stroke-width="1.8"><circle cx="12" cy="12" r="10"/><ellipse cx="12" cy="12" rx="4.5" ry="10"/><path d="M2 12h20M4 7h16M4 17h16"/></g></svg>
        <span><strong>resinworkshub</strong>.ca</span>
      </li>
    </ul>
  </section>

  <section class="card card--back">
    <p class="brand-name--large">Resin Works Hub</p>
  </section>
</body>
</html>
```